Website Design for Employee Moral and Happiness Company

Looking for a clean website design that explains our features in a step by step manner so our visitors know exactly what our site does before logging in.

The site is called "Velrato". See logo design and video for a sample of style and an overview of what we do.

Target Market(s)

Business owners that are looking to retain employees.

Number of Pages Required

1 page

```html
<!DOCTYPE html>
<html lang="en">
<head>
<meta charset="utf-8">
<title>Velrato – Employee Morale and Happiness</title>
<link href="https://fonts.googleapis.com/css2?family=Roboto:wght@400;500;700&family=Roboto+Condensed:wght@700&display=swap" rel="stylesheet">
<style>
:root{
  --orange:#f15a22;
  --orange-dark:#d8491a;
  --ink:#1a1a1a;
  --text:#555;
  --muted:#888;
  --line:#e3e3e3;
  --soft:#efefef;
  --white:#fff;
  --footer:#111;
}
*{box-sizing:border-box;margin:0;padding:0}
html,body{width:1200px;height:3776px;overflow:hidden}
body{font-family:"Roboto",Arial,sans-serif;color:var(--text);background:var(--white);font-size:15px;line-height:1.55}
h1,h2,h3,h4{font-family:"Roboto Condensed","Arial Narrow",sans-serif;color:var(--ink);text-transform:uppercase}
.section-title{text-align:center;font-size:34px;letter-spacing:.5px}
.btn{display:inline-flex;align-items:center;gap:8px;background:var(--orange);color:var(--white);font-weight:700;font-size:13px;text-transform:uppercase;padding:12px 22px;border-radius:3px;letter-spacing:.5px}

/* header + hero */
.hero{position:relative;height:704px;background:linear-gradient(100deg,#3a3330 0%,#6b5a4f 38%,#c9b7a4 62%,#e8ddd2 80%,#9c8878 100%)}
.hero::after{content:"";position:absolute;inset:0;background:linear-gradient(90deg,rgba(0,0,0,.55),rgba(0,0,0,.1) 55%,rgba(0,0,0,0))}
.topbar{position:absolute;z-index:2;top:0;left:0;right:0;height:72px;background:var(--white);display:flex;align-items:center;padding:0 100px 0 100px}
.logo{font-family:"Roboto",sans-serif;font-weight:700;font-size:34px;color:var(--orange);letter-spacing:-.5px}
.nav{display:flex;gap:26px;margin-left:auto;font-size:13px;font-weight:500;text-transform:uppercase;color:var(--ink)}
.nav .active{background:var(--orange);color:var(--white);padding:4px 10px;margin:-4px -10px}
.top-phone{display:flex;align-items:center;gap:8px;margin-left:34px;font-size:13px;font-weight:700;color:var(--ink)}
.icon-dot{width:28px;height:28px;border-radius:50%;background:var(--orange);display:flex;align-items:center;justify-content:center;flex:none}
.top-login{margin-left:26px;padding:8px 16px}
.hero-copy{position:absolute;z-index:2;left:130px;top:290px;width:460px}
.hero-copy h1{color:var(--white);font-size:44px;margin-bottom:14px}
.hero-copy p{color:#eee;font-size:15px;margin-bottom:26px}
.hero-arrow{position:absolute;z-index:2;top:370px;width:40px;height:40px;border-radius:50%;background:var(--white);display:flex;align-items:center;justify-content:center}
.hero-arrow.left{left:36px}.hero-arrow.right{right:36px}

/* features */
.features{height:456px;padding-top:62px}
.feature-row{display:flex;justify-content:center;gap:34px;margin-top:44px}
.feature-card{position:relative;width:222px;height:260px}
.feature-card .card-bg{position:absolute;inset:0}
.feature-body{position:absolute;top:104px;left:22px;right:22px}
.feature-body h3{font-size:14px;margin-bottom:6px}
.feature-body p{font-size:13px;line-height:1.45}
.feature-num{position:absolute;top:18px;left:50%;transform:translateX(-50%);font-family:"Roboto Condensed",sans-serif;font-weight:700;font-size:40px;color:var(--white)}
.feature-icon{position:absolute;bottom:16px;left:50%;transform:translateX(-50%)}

/* about */
.about{height:600px;background:var(--soft);display:flex;align-items:center;padding:0 130px;gap:50px}
.collage{position:relative;width:450px;height:380px;flex:none}
.ph{position:absolute;border:5px solid var(--white);box-shadow:0 4px 14px rgba(0,0,0,.15)}
.about-copy h2{font-size:34px;margin-bottom:14px}
.about-copy p{font-size:15px;margin-bottom:22px}

/* testimonials */
.testimonials{height:520px;padding-top:62px}
.testi-row{display:flex;justify-content:center;gap:40px;margin-top:44px}
.testi-card{width:470px;border:1px solid var(--line);box-shadow:0 3px 12px rgba(0,0,0,.08);padding:48px 28px 26px;position:relative;background:var(--white)}
.quote{position:absolute;top:-20px;left:28px;width:42px;height:42px;border-radius:50%;background:var(--orange);display:flex;align-items:center;justify-content:center}
.testi-card h4{font-size:15px;margin-bottom:10px}
.testi-card p{font-size:13px;margin-bottom:18px}
.person{display:flex;align-items:center;gap:14px}
.avatar{width:44px;height:44px;border-radius:50%;background:linear-gradient(135deg,#999,#666)}
.person strong{display:block;font-size:13px;color:var(--ink);text-transform:uppercase}
.stars{color:var(--orange);letter-spacing:2px;font-size:14px}

/* news */
.news{height:640px;background:linear-gradient(160deg,var(--orange) 0%,#e8521d 50%,var(--orange-dark) 100%);padding-top:58px}
.news .section-title{color:var(--white)}
.news-row{display:flex;justify-content:center;gap:28px;margin-top:40px}
.news-card{width:300px;background:var(--white);position:relative}
.news-img{height:170px}
.news-tag{position:absolute;top:0;right:14px;width:34px;height:38px;background:var(--orange);display:flex;align-items:center;justify-content:center}
.news-body{padding:16px 22px 22px}
.meta{display:flex;gap:18px;font-size:12px;color:var(--muted);margin-bottom:8px}
.meta span::before{content:"";display:inline-block;width:9px;height:9px;background:var(--orange);margin-right:6px;border-radius:2px}
.news-body h4{font-size:15px;margin-bottom:8px}
.news-body p{font-size:13px;margin-bottom:12px}
.read{font-size:13px;font-weight:700;color:var(--orange);display:flex;align-items:center;gap:8px}

/* contact */
.contact{height:520px;display:flex;padding:80px 140px 0;gap:80px;background:linear-gradient(180deg,#f6f6f6,#fff)}
.contact-info{width:420px}
.contact-info h2{font-size:32px;margin-bottom:10px}
.contact-info>p{font-size:15px;margin-bottom:22px}
.c-line{display:flex;align-items:center;gap:14px;font-size:14px;color:var(--ink);margin-bottom:18px}
.c-line .icon-dot{width:36px;height:36px}
.form{flex:1;display:grid;grid-template-columns:1fr 1fr;gap:14px;align-content:start}
.field{height:42px;border:1px solid var(--line);background:var(--white);display:flex;align-items:center;gap:8px;padding:0 14px;font-size:13px;color:var(--muted)}
.field.wide{grid-column:1/3;height:120px;align-items:flex-start;padding-top:12px}
.field::before{content:"";width:8px;height:8px;border-radius:50%;background:var(--orange);flex:none}
.field.wide::before{margin-top:5px}
.submit{grid-column:2;justify-self:end}

/* footer */
.footer{height:336px;background:var(--footer);color:#bbb;padding:56px 100px 0;position:relative}
.foot-cols{display:flex;gap:70px}
.foot-brand{width:300px}
.foot-brand .logo{color:var(--white);display:block;margin-bottom:10px}
.foot-brand p{font-size:13px;margin-bottom:16px}
.footer h4{color:var(--white);font-size:15px;margin-bottom:16px}
.socials{display:flex;gap:10px}
.socials span{width:32px;height:32px;border-radius:50%;border:1.5px solid #888}
.foot-list{list-style:none;font-size:13px}
.foot-list li{margin-bottom:10px;display:flex;align-items:center;gap:10px}
.foot-list li::before{content:"";width:6px;height:6px;background:var(--orange);border-radius:50%}
.foot-contact li::before{display:none}
.foot-contact .icon-dot{width:26px;height:26px}
.copyright{position:absolute;left:0;right:0;bottom:0;height:44px;border-top:1px solid #2c2c2c;text-align:center;line-height:44px;font-size:12px;color:#888}
</style>
</head>
<body>

<header class="hero">
  <div role="img" aria-label="Photo of a smiling team at work in a bright office" style="position:absolute;inset:0"></div>
  <div class="topbar">
    <span class="logo">Velrato</span>
    <nav class="nav">
      <span class="active">Home</span><span>About Us</span><span>Features</span><span>Testimonials</span><span>News</span><span>Contact Us</span>
    </nav>
    <span class="top-phone"><span class="icon-dot"><svg width="14" height="14" viewBox="0 0 24 24"><path fill="#fff" d="M6.6 10.8a15 15 0 0 0 6.6 6.6l2.2-2.2c.3-.3.7-.4 1-.2 1.1.4 2.3.6 3.6.6.6 0 1 .4 1 1V20c0 .6-.4 1-1 1A17 17 0 0 1 3 4c0-.6.4-1 1-1h3.5c.6 0 1 .4 1 1 0 1.3.2 2.5.6 3.6.1.3 0 .7-.2 1z"/></svg></span>+1 888 888 8888</span>
    <span class="btn top-login">Login <svg width="10" height="10" viewBox="0 0 10 10"><path d="M2 5h6M5 2l3 3-3 3" stroke="#fff" stroke-width="1.6" fill="none"/></svg></span>
  </div>
  <div class="hero-copy">
    <h1>Welcome to Velrato</h1>
    <p>Lorem ipsum dolor sit amet, consectetur adipiscing elit, sed do eiusmod tempor incididunt ut labore et dolore magna aliqua.</p>
    <span class="btn">Get Started <svg width="10" height="10" viewBox="0 0 10 10"><path d="M2 5h6M5 2l3 3-3 3" stroke="#fff" stroke-width="1.6" fill="none"/></svg></span>
  </div>
  <span class="hero-arrow left"><svg width="12" height="12" viewBox="0 0 12 12"><path d="M8 2 4 6l4 4" stroke="#222" stroke-width="2" fill="none"/></svg></span>
  <span class="hero-arrow right"><svg width="12" height="12" viewBox="0 0 12 12"><path d="m4 2 4 4-4 4" stroke="#222" stroke-width="2" fill="none"/></svg></span>
</header>

<section class="features">
  <h2 class="section-title">Our Features</h2>
  <div class="feature-row">
    <!-- card template repeated with alternating accent -->
    <div class="feature-card">
      <svg class="card-bg" width="222" height="260" viewBox="0 0 222 260"><path d="M0 0h222v215l-111 45L0 215z" fill="#fff" stroke="#e3e3e3"/><path d="M40 0h142v66l-71 22-71-22z" fill="#f15a22"/><path d="M70 215l41 17 41-17v35l-41 10-41-10z" fill="#f15a22"/></svg>
      <span class="feature-num">01</span>
      <div class="feature-body"><h3>Lorem ipsum dolor amet</h3><p>Lorem ipsum dolor sit amet, consectetur adipiscing elit, sed do eiusmod tempor incididunt labore.</p></div>
      <svg class="feature-icon" width="24" height="24" viewBox="0 0 24 24"><circle cx="12" cy="12" r="9" fill="none" stroke="#fff" stroke-width="2"/><path d="m8 12 3 3 5-6" stroke="#fff" stroke-width="2" fill="none"/></svg>
    </div>
    <div class="feature-card">
      <svg class="card-bg" width="222" height="260" viewBox="0 0 222 260"><path d="M0 0h222v215l-111 45L0 215z" fill="#fff" stroke="#e3e3e3"/><path d="M40 0h142v66l-71 22-71-22z" fill="#1a1a1a"/><path d="M70 215l41 17 41-17v35l-41 10-41-10z" fill="#1a1a1a"/></svg>
      <span class="feature-num">02</span>
      <div class="feature-body"><h3>Lorem ipsum dolor amet</h3><p>Lorem ipsum dolor sit amet, consectetur adipiscing elit, sed do eiusmod tempor incididunt labore.</p></div>
      <svg class="feature-icon" width="24" height="24" viewBox="0 0 24 24"><circle cx="12" cy="7" r="4" fill="#fff"/><path d="M4 21c0-5 4-7 8-7s8 2 8 7z" fill="#fff"/></svg>
    </div>
    <div class="feature-card">
      <svg class="card-bg" width="222" height="260" viewBox="0 0 222 260"><path d="M0 0h222v215l-111 45L0 215z" fill="#fff" stroke="#e3e3e3"/><path d="M40 0h142v66l-71 22-71-22z" fill="#f15a22"/><path d="M70 215l41 17 41-17v35l-41 10-41-10z" fill="#f15a22"/></svg>
      <span class="feature-num">03</span>
      <div class="feature-body"><h3>Lorem ipsum dolor amet</h3><p>Lorem ipsum dolor sit amet, consectetur adipiscing elit, sed do eiusmod tempor incididunt labore.</p></div>
      <svg class="feature-icon" width="24" height="24" viewBox="0 0 24 24"><circle cx="12" cy="12" r="4" fill="#fff"/><circle cx="12" cy="12" r="8" fill="none" stroke="#fff" stroke-width="2" stroke-dasharray="3 3"/></svg>
    </div>
    <div class="feature-card">
      <svg class="card-bg" width="222" height="260" viewBox="0 0 222 260"><path d="M0 0h222v215l-111 45L0 215z" fill="#fff" stroke="#e3e3e3"/><path d="M40 0h142v66l-71 22-71-22z" fill="#1a1a1a"/><path d="M70 215l41 17 41-17v35l-41 10-41-10z" fill="#1a1a1a"/></svg>
      <span class="feature-num">04</span>
      <div class="feature-body"><h3>Lorem ipsum dolor amet</h3><p>Lorem ipsum dolor sit amet, consectetur adipiscing elit, sed do eiusmod tempor incididunt labore.</p></div>
      <svg class="feature-icon" width="24" height="24" viewBox="0 0 24 24"><path d="M3 20h18M6 20V10M12 20V5M18 20v-7" stroke="#fff" stroke-width="2.5"/></svg>
    </div>
  </div>
</section>

<section class="about">
  <div class="collage">
    <div class="ph" role="img" aria-label="Photo of colleagues smiling together" style="left:0;top:10px;width:200px;height:170px;background:linear-gradient(135deg,#d9cfc4,#8a7869)"></div>
    <div class="ph" role="img" aria-label="Photo of a team meeting around a table" style="left:210px;top:0;width:240px;height:180px;background:linear-gradient(135deg,#b7b3ad,#4f5560)"></div>
    <div class="ph" role="img" aria-label="Photo of a group discussion in an office" style="left:40px;top:190px;width:190px;height:180px;background:linear-gradient(135deg,#6d7782,#2f3640)"></div>
    <div class="ph" role="img" aria-label="Photo of coworkers reviewing work on a laptop" style="left:240px;top:190px;width:210px;height:180px;background:linear-gradient(135deg,#c8b9a6,#6e5c4d)"></div>
    <div style="position:absolute;left:0;top:260px;width:40px;height:40px;background:var(--orange)"></div>
  </div>
  <div class="about-copy">
    <h2>About Us</h2>
    <p>Lorem ipsum dolor sit amet, consectetur adipiscing elit, sed do eiusmod tempor incididunt ut labore et dolore magna aliqua. Ut enim ad minim veniam, quis nostrud exercitation ullamco laboris nisi ut aliquip ex ea commodo consequat. Duis aute irure dolor in reprehenderit in voluptate velit esse cillum dolore eu fugiat nulla pariatur. Excepteur sint occaecat cupidatat non proident, sunt in culpa qui officia deserunt mollit anim id est laborum.</p>
    <span class="btn">Learn More <svg width="10" height="10" viewBox="0 0 10 10"><path d="M2 5h6M5 2l3 3-3 3" stroke="#fff" stroke-width="1.6" fill="none"/></svg></span>
  </div>
</section>

<section class="testimonials">
  <h2 class="section-title">Our Testimonials</h2>
  <div class="testi-row">
    <article class="testi-card">
      <span class="quote"><svg width="18" height="14" viewBox="0 0 18 14"><path d="M0 14V7L4 0h3L5 6h3v8zm10 0V7l4-7h3l-2 6h3v8z" fill="#fff"/></svg></span>
      <h4>Lorem ipsum dolor sit amet consectetur adipisci</h4>
      <p>Lorem ipsum dolor sit amet, consectetur adipiscing elit, sed do eiusmod tempor incididunt ut labore et dolore magna aliqua. Ut enim ad minim veniam, quis nostrud exercitation ullamco laboris nisi ut aliquip ex ea commodo consequat.</p>
      <div class="person"><span class="avatar" role="img" aria-label="Client portrait"></span><div><strong>Mara Lindqvist</strong><span class="stars">★★★★★</span></div></div>
    </article>
    <article class="testi-card">
      <span class="quote"><svg width="18" height="14" viewBox="0 0 18 14"><path d="M0 14V7L4 0h3L5 6h3v8zm10 0V7l4-7h3l-2 6h3v8z" fill="#fff"/></svg></span>
      <h4>Lorem ipsum dolor sit amet consectetur adipisci</h4>
      <p>Lorem ipsum dolor sit amet, consectetur adipiscing elit, sed do eiusmod tempor incididunt ut labore et dolore magna aliqua. Ut enim ad minim veniam, quis nostrud exercitation ullamco laboris nisi ut aliquip ex ea commodo consequat.</p>
      <div class="person"><span class="avatar" role="img" aria-label="Client portrait"></span><div><strong>Mara Lindqvist</strong><span class="stars">★★★★★</span></div></div>
    </article>
  </div>
</section>

<section class="news">
  <h2 class="section-title">Latest News</h2>
  <div class="news-row">
    <article class="news-card">
      <div class="news-img" role="img" aria-label="Photo of a team celebrating at work" style="background:linear-gradient(135deg,#cbbfb2,#5f5148)"></div>
      <span class="news-tag"><svg width="14" height="14" viewBox="0 0 14 14"><rect x="1" y="2" width="12" height="11" fill="none" stroke="#fff" stroke-width="1.5"/><path d="M1 5h12" stroke="#fff" stroke-width="1.5"/></svg></span>
      <div class="news-body"><div class="meta"><span>29.5.2022</span><span>Comments</span></div><h4>Lorem ipsum admin consectetur</h4><p>Lorem ipsum dolor sit amet consectetur adipiscing elit, sed do eiusmod tempor incididunt ut labore.</p><span class="read">Read More <svg width="14" height="14" viewBox="0 0 14 14"><circle cx="7" cy="7" r="7" fill="#f15a22"/><path d="M5 4l3 3-3 3" stroke="#fff" stroke-width="1.5" fill="none"/></svg></span></div>
    </article>
    <article class="news-card">
      <div class="news-img" role="img" aria-label="Photo of a workshop session" style="background:linear-gradient(135deg,#8f9aa3,#3c424a)"></div>
      <span class="news-tag"><svg width="14" height="14" viewBox="0 0 14 14"><rect x="1" y="2" width="12" height="11" fill="none" stroke="#fff" stroke-width="1.5"/><path d="M1 5h12" stroke="#fff" stroke-width="1.5"/></svg></span>
      <div class="news-body"><div class="meta"><span>29.5.2022</span><span>Comments</span></div><h4>Lorem ipsum admin consectetur</h4><p>Lorem ipsum dolor sit amet consectetur adipiscing elit, sed do eiusmod tempor incididunt ut labore.</p><span class="read">Read More <svg width="14" height="14" viewBox="0 0 14 14"><circle cx="7" cy="7" r="7" fill="#f15a22"/><path d="M5 4l3 3-3 3" stroke="#fff" stroke-width="1.5" fill="none"/></svg></span></div>
    </article>
    <article class="news-card">
      <div class="news-img" role="img" aria-label="Photo of colleagues talking at a desk" style="background:linear-gradient(135deg,#d8cdbf,#7a6a5c)"></div>
      <span class="news-tag"><svg width="14" height="14" viewBox="0 0 14 14"><rect x="1" y="2" width="12" height="11" fill="none" stroke="#fff" stroke-width="1.5"/><path d="M1 5h12" stroke="#fff" stroke-width="1.5"/></svg></span>
      <div class="news-body"><div class="meta"><span>29.5.2022</span><span>Comments</span></div><h4>Lorem ipsum admin consectetur</h4><p>Lorem ipsum dolor sit amet consectetur adipiscing elit, sed do eiusmod tempor incididunt ut labore.</p><span class="read">Read More <svg width="14" height="14" viewBox="0 0 14 14"><circle cx="7" cy="7" r="7" fill="#f15a22"/><path d="M5 4l3 3-3 3" stroke="#fff" stroke-width="1.5" fill="none"/></svg></span></div>
    </article>
  </div>
</section>

<section class="contact">
  <div class="contact-info">
    <h2>Contact With Us</h2>
    <p>Lorem ipsum dolor sit amet, consectetur adipiscing elit, sed do eiusmod tempor incididunt ut labore.</p>
    <div class="c-line"><span class="icon-dot"><svg width="16" height="16" viewBox="0 0 24 24"><path fill="#fff" d="M6.6 10.8a15 15 0 0 0 6.6 6.6l2.2-2.2c.3-.3.7-.4 1-.2 1.1.4 2.3.6 3.6.6.6 0 1 .4 1 1V20c0 .6-.4 1-1 1A17 17 0 0 1 3 4c0-.6.4-1 1-1h3.5c.6 0 1 .4 1 1 0 1.3.2 2.5.6 3.6.1.3 0 .7-.2 1z"/></svg></span>+1 888 888 8888</div>
    <div class="c-line"><span class="icon-dot"><svg width="16" height="16" viewBox="0 0 24 24"><rect x="3" y="5" width="18" height="14" fill="none" stroke="#fff" stroke-width="2"/><path d="m3 6 9 7 9-7" stroke="#fff" stroke-width="2" fill="none"/></svg></span>info@velrato.com</div>
    <div class="c-line"><span class="icon-dot"><svg width="16" height="16" viewBox="0 0 24 24"><path fill="#fff" d="M12 2a7 7 0 0 0-7 7c0 5 7 13 7 13s7-8 7-13a7 7 0 0 0-7-7zm0 9.5A2.5 2.5 0 1 1 12 6.5a2.5 2.5 0 0 1 0 5z"/></svg></span>1234 Lorem ipsum dolor sit amet consectetur<br>adipiscing elit sed do eiusmod tempor</div>
  </div>
  <form class="form">
    <span class="field">First Name</span><span class="field">Last Name</span>
    <span class="field">Email</span><span class="field">Phone</span>
    <span class="field wide">Comments</span>
    <span class="btn submit">Submit <svg width="10" height="10" viewBox="0 0 10 10"><path d="M2 5h6M5 2l3 3-3 3" stroke="#fff" stroke-width="1.6" fill="none"/></svg></span>
  </form>
</section>

<footer class="footer">
  <div class="foot-cols">
    <div class="foot-brand">
      <span class="logo">Velrato</span>
      <p>Sed ut perspiciatis unde omnis iste natus error sit voluptatem accusantium doloremque.</p>
      <h4>Follow Us</h4>
      <div class="socials"><span></span><span></span><span></span><span></span></div>
    </div>
    <div>
      <h4>Contact Us</h4>
      <ul class="foot-list foot-contact">
        <li><span class="icon-dot"><svg width="12" height="12" viewBox="0 0 24 24"><path fill="#fff" d="M6.6 10.8a15 15 0 0 0 6.6 6.6l2.2-2.2c.3-.3.7-.4 1-.2 1.1.4 2.3.6 3.6.6.6 0 1 .4 1 1V20c0 .6-.4 1-1 1A17 17 0 0 1 3 4c0-.6.4-1 1-1h3.5c.6 0 1 .4 1 1 0 1.3.2 2.5.6 3.6.1.3 0 .7-.2 1z"/></svg></span>+1 888 888 8888</li>
        <li><span class="icon-dot"><svg width="12" height="12" viewBox="0 0 24 24"><rect x="3" y="5" width="18" height="14" fill="none" stroke="#fff" stroke-width="2"/><path d="m3 6 9 7 9-7" stroke="#fff" stroke-width="2" fill="none"/></svg></span>info@velrato.com</li>
        <li><span class="icon-dot"><svg width="12" height="12" viewBox="0 0 24 24"><path fill="#fff" d="M12 2a7 7 0 0 0-7 7c0 5 7 13 7 13s7-8 7-13a7 7 0 0 0-7-7z"/></svg></span>1234 Lorem ipsum dolor<br>consectetur adipiscing</li>
      </ul>
    </div>
    <div>
      <h4>Quicklinks</h4>
      <ul class="foot-list"><li>Home</li><li>About us</li><li>Features</li><li>Testimonials</li><li>News</li><li>Contact us</li></ul>
    </div>
    <div>
      <h4>Otherlinks</h4>
      <ul class="foot-list"><li>Team</li><li>FAQ</li><li>Services</li><li>Privacy</li><li>Policy</li></ul>
    </div>
  </div>
  <div class="copyright">© 2022 Copyright Velrato. All Rights Reserved.</div>
</footer>

</body>
</html>
```